Trading Company needs a business card design, letter head design and email signature

We need a double-sided business card design, letter head design and an email signature. We have a logo design.

Possible Tag Lines:
• “Connecting Worlds, Building Excellence.”
• “Global Sourcing, Local Excellence.”
• “Bridging Borders, Building Quality.”
• “Worldwide Partnerships, Superior Goods.”
• “Where Quality Meets Affordability”

Services Offered:
Procurement
Fabrication
Distribution
Logistics
Import/Export

Requirements
Must have
• Nice quality double sided Business Card design, Letterhead design needs to be A4
Nice to have
• possible ideas on tag lines

```html
<!DOCTYPE html>
<html lang="en">
<head>
<meta charset="utf-8">
<title>Corvane Letterhead</title>
<link href="https://fonts.googleapis.com/css2?family=Open+Sans:wght@400;600;700&display=swap" rel="stylesheet">
<style>
  :root {
    --brand-red: #ed1f24;
    --ink: #2b2b2b;
    --swoosh-grey: #4d4f51;
    --paper: #ffffff;
    --backdrop: #d9d9d9;
    --mark-tint: #efefef;
  }
  * { margin: 0; padding: 0; box-sizing: border-box; }
  html, body { width: 1200px; height: 686px; overflow: hidden; }
  body {
    background: var(--backdrop);
    font-family: "Open Sans", Arial, sans-serif;
    position: relative;
  }
  .letterhead {
    position: absolute;
    left: 380px;
    top: 32px;
    width: 440px;
    height: 622px;
    background: var(--paper);
    box-shadow: 0 6px 22px rgba(0,0,0,0.18);
    overflow: hidden;
  }
  .brand {
    position: absolute;
    left: 62px;
    top: 48px;
    display: flex;
    align-items: center;
    gap: 8px;
  }
  .brand-square {
    width: 16px;
    height: 16px;
    background: var(--brand-red);
  }
  .brand-name {
    font-weight: 700;
    font-size: 20px;
    letter-spacing: 2px;
    color: var(--brand-red);
    text-transform: uppercase;
  }
  .contact {
    position: absolute;
    left: 288px;
    top: 30px;
    padding-left: 10px;
    border-left: 1.5px solid var(--brand-red);
    font-size: 7.5px;
    line-height: 11px;
    color: var(--ink);
  }
  .contact-row { display: flex; align-items: center; gap: 5px; }
  .contact-row svg { width: 7px; height: 7px; flex: none; }
  .contact-row .spacer { width: 7px; flex: none; }
  .watermark-block {
    position: absolute;
    left: 115px;
    top: 205px;
    width: 210px;
    height: 210px;
    background: var(--mark-tint);
  }
  .footer-band {
    position: absolute;
    left: 0;
    bottom: 0;
    width: 440px;
    height: 150px;
  }
  .taglines {
    position: absolute;
    left: 14px;
    top: 594px;
    font-size: 6px;
    line-height: 9px;
    color: var(--paper);
  }
  .taglines p { display: flex; align-items: center; gap: 4px; white-space: nowrap; }
  .taglines .indent-1 { padding-left: 10px; }
  .taglines .indent-2 { padding-left: 22px; }
  .bullet {
    display: inline-block;
    width: 4px;
    height: 4px;
    background: var(--paper);
  }
</style>
</head>
<body>
  <main class="letterhead">
    <div class="brand">
      <span class="brand-square"></span>
      <span class="brand-name">Corvane</span>
    </div>

    <address class="contact" style="font-style:normal">
      <div class="contact-row"><span class="spacer"></span>212 Harbour Lane,</div>
      <div class="contact-row"><span class="spacer"></span>Dover, Kent, CT16 2AB</div>
      <div class="contact-row">
        <svg viewBox="0 0 10 10"><path d="M2 1 L4 1 L5 3.5 L3.8 4.5 Q4.8 6 5.8 6.4 L6.6 5.2 L9 6.2 L9 8.2 Q5 9.5 2.2 6 Q0.6 3.8 2 1Z" fill="var(--brand-red)"/></svg>
        (555) 014-2273
      </div>
      <div class="contact-row">
        <svg viewBox="0 0 10 10"><circle cx="5" cy="5" r="4" fill="none" stroke="var(--brand-red)" stroke-width="1.2"/><ellipse cx="5" cy="5" rx="1.8" ry="4" fill="none" stroke="var(--brand-red)" stroke-width="1"/><line x1="1" y1="5" x2="9" y2="5" stroke="var(--brand-red)" stroke-width="1"/></svg>
        www.corvanetrading.com
      </div>
      <div class="contact-row">
        <svg viewBox="0 0 10 10"><rect x="0.8" y="2" width="8.4" height="6" fill="var(--brand-red)"/><path d="M0.8 2 L5 5.5 L9.2 2" fill="none" stroke="#fff" stroke-width="0.9"/></svg>
        info@corvanetrading.com
      </div>
    </address>

    <div class="watermark-block" aria-hidden="true"></div>

    <svg class="footer-band" viewBox="0 472 440 150" aria-hidden="true">
      <path d="M0 490 C 100 565 250 595 440 604 L440 622 L0 622 Z" fill="var(--brand-red)"/>
      <path d="M14 476 C 110 552 262 585 430 596" fill="none" stroke="var(--swoosh-grey)" stroke-width="2" stroke-linecap="round"/>
    </svg>

    <div class="taglines">
      <p><span class="bullet"></span>Connecting Worlds, Building Excellence <span class="bullet"></span>Global Sourcing, Local Excellence</p>
      <p class="indent-1"><span class="bullet"></span>Bridging Borders, Building Quality <span class="bullet"></span>Worldwide Partnerships, Superior Goods</p>
      <p class="indent-2"><span class="bullet"></span>Where Quality Meets Affordability</p>
    </div>
  </main>
</body>
</html>
```